KVR Inc Web Design

WHAT ARE WE DOING?
We are developing a new website look and feel for a new company called KVR Inc. This new look and feel should include colors, design elements, choice of photography and other imagery, fonts, and other user experience elements.

WHAT DO THEY DO?
KVR, Inc, makes tools for researchers who are studying protein-protein interactions. These molecules are the basic tools of biology, and serve as key targets for drug developers and disease researchers. The world of proteins is enormously complex, and companies like KVR provide researchers with critical tools that help them elucidate this world.

WHO ARE WE TALKING TO?
The target audience for this website are professional scientists working in university research or biopharma drug development. They are highly sophisticated consumers looking for key tools that will advance their research.

WHAT DO WE WANT THEM TO DO?
The site is an information resource for the customer exploring the tools that KVR sells and the scientific issues surrounding protein-protein interactions. They should be able to navigate easily to their content of choice, while the whole site should convey a professionalism that enhanced KVR’s credibility.

WHAT DOES THE KVR BRAND STAND FOR?
KVR stands for illumination. Proteins are challenging to study, and KVR exists to help shed light on their workings.

WHAT ARE THE KEY VALUES OF THE KVR BRAND?
Integrity. Innovation. Insight.

WHAT ARE THE EXECUTIONAL MANDITORIES?
The look and feel is completely up for grabs. Nothing is off the table.

WHAT ARE THE DELIVERABLES?
We need new designs for the following templates:
http://cms.marlowbench.com/
http://cms.marlowbench.com/products-and-services/instruments-3/bench-top-instruments/
http://cms.marlowbench.com/category/lab-study/

```html
<!DOCTYPE html>
<html lang="en">
<head>
<meta charset="utf-8">
<title>KVR Inc — Events</title>
<link href="https://fonts.googleapis.com/css2?family=Figtree:ital,wght@0,300;0,400;0,600;0,700;1,400&display=swap" rel="stylesheet">
<style>
  :root{
    --orange:#f7a823;
    --blue:#35aed0;
    --text:#555;
    --muted:#8a8a8a;
    --rule:#d6d6d6;
    --footer:#6b6b6b;
    --white:#fff;
  }
  *{box-sizing:border-box;margin:0;padding:0}
  html,body{width:1039px;height:1200px;overflow:hidden;background:var(--white)}
  body{font-family:"Figtree",Arial,sans-serif;color:var(--text);position:relative}
  a{text-decoration:none;color:inherit}

  .site-header{position:absolute;top:0;left:0;width:1039px;height:53px;border-top:2px solid var(--orange);border-bottom:1px solid #e6e6e6;box-shadow:0 1px 2px rgba(0,0,0,.04)}
  .brand{position:absolute;left:104px;top:12px;font-size:24px;font-weight:300;letter-spacing:6px;color:#707070;line-height:26px}
  .main-nav{position:absolute;left:264px;top:16px;display:flex;gap:19.5px;font-size:14px;font-weight:600;color:#666}
  .main-nav .is-active{color:var(--orange)}
  .search{position:absolute;left:816px;top:14px;width:119px;height:21px;background:linear-gradient(#8d8d8d,#9f9f9f);border-radius:2px;display:flex;align-items:center;padding-left:6px;font-size:11px;color:#eee}
  .search svg{position:absolute;right:6px;top:4px}

  .sidebar{position:absolute;left:103px;top:78px;width:192px}
  .side-title{font-size:15.5px;font-weight:600;color:var(--blue);height:30px;border-bottom:3px double var(--rule);padding-top:1px}
  .side-list{list-style:none}
  .side-list li{height:29.2px;border-bottom:1px solid #e8e8e8;font-size:13.5px;display:flex;align-items:center;padding-left:11px;position:relative;color:#666}
  .side-list li::before{content:"»";position:absolute;left:0;top:6px;font-size:11px;color:#555}
  .side-list li.is-active{color:var(--orange)}
  .side-list li.is-active::before{color:var(--orange)}
  .side-list li.is-active::after{content:"";position:absolute;right:12px;top:14px;width:18px;height:1px;background:var(--orange)}
  .side-list li:last-child{border-bottom:none}
  .archive{margin-top:47px}

  .content{position:absolute;left:317px;top:72px;width:618px}
  .page-title{height:36px;border-bottom:3px double var(--rule);display:flex;align-items:center;gap:12px;font-size:23px;font-weight:300;letter-spacing:.5px;color:#666;padding-bottom:4px}
  .event{position:absolute;left:0;width:630px;height:174px}
  .event-photo{position:absolute;left:0;top:0;width:226px;height:174px;border:1px solid #ddd;padding:5px;background:var(--white)}
  .event-photo div{width:100%;height:100%}
  .event-body{position:absolute;left:242px;top:0;width:385px}
  .event-title{font-size:18px;font-weight:400;color:var(--blue);margin-top:0;line-height:22px}
  .event-title.alt{color:var(--orange)}
  .event-date{font-size:11.5px;font-style:italic;color:var(--muted);margin-top:5px}
  .event-text{font-size:11px;line-height:16.2px;margin-top:5px;color:#555}
  .learn-more{display:inline-block;margin-top:7px;font-size:12px;color:var(--orange)}

  .site-footer{position:absolute;left:0;top:1146px;width:1039px;height:54px;background:var(--footer);color:var(--white)}
  .footer-nav{position:absolute;left:104px;top:22px;font-size:10.5px;display:flex;gap:6px}
  .social{position:absolute;left:713px;top:18px;display:flex;gap:6px}
  .social span{width:21px;height:21px;border-radius:50%;background:var(--white)}
  .copyright{position:absolute;left:804px;top:22px;font-size:11.5px}
  .copyright em{font-style:normal;color:var(--orange)}
</style>
</head>
<body>
<header class="site-header">
  <div class="brand">KVR INC</div>
  <nav class="main-nav">
    <a href="#">Company</a><a href="#" class="is-active">Products &amp; Services</a><a href="#">Learning Center</a><a href="#">Events</a><a href="#">KVR News</a><a href="#">Contact</a>
  </nav>
  <div class="search">Search
    <svg width="12" height="12" viewBox="0 0 12 12"><circle cx="5" cy="5" r="3.7" fill="none" stroke="#cfcfcf" stroke-width="1.3"/><line x1="7.7" y1="7.7" x2="11" y2="11" stroke="#cfcfcf" stroke-width="1.5"/></svg>
  </div>
</header>

<aside class="sidebar">
  <h3 class="side-title">Categories</h3>
  <ul class="side-list">
    <li>Conferences</li><li class="is-active">Press Releases</li><li>Product Announcements</li><li>Seminars</li><li>Webinars</li>
  </ul>
  <div class="archive">
    <h3 class="side-title">Archive</h3>
    <ul class="side-list"><li>&nbsp;2013</li><li>2012</li><li>2011</li></ul>
  </div>
</aside>

<main class="content">
  <h1 class="page-title">
    <svg width="25" height="25" viewBox="0 0 25 25"><rect x="1.5" y="4" width="22" height="19.5" fill="none" stroke="#666" stroke-width="2.4"/><rect x="1.5" y="4" width="22" height="5" fill="#666"/><rect x="6" y="0.5" width="2.5" height="5" fill="#666"/><rect x="16.5" y="0.5" width="2.5" height="5" fill="#666"/><polyline points="7.5,15 11,18.5 18,11.5" fill="none" stroke="#666" stroke-width="2.4"/></svg>
    EVENTS
  </h1>

  <article class="event" style="top:58px">
    <div class="event-photo"><div role="img" aria-label="Two scientists in caps and masks working at microscopes" style="background:linear-gradient(135deg,#cfe2f1,#9fbfd6 45%,#e8eef3)"></div></div>
    <div class="event-body">
      <h2 class="event-title">Aliquam Commodo</h2>
      <p class="event-date">Oct 10, 2013</p>
      <p class="event-text">Quisque feugiat lacus vitae posuere blandit. Nulla sit amet laoreet felis, id rhoncus nisl. Aenean fringilla quam in nibh egestas, in malesuada tortor accumsan. Donec non massa lacinia, commodo eros eget, rutrum arcu. Integer tincidunt, velit id eleifend congue, odio massa consequat mauris, a scelerisque nulla nulla eu nulla. Cras luctus pulvinar nibh...</p>
      <a class="learn-more" href="#">Learn More &nbsp;»</a>
    </div>
  </article>

  <article class="event" style="top:260px">
    <div class="event-photo"><div role="img" aria-label="Two researchers in lab coats examining test tubes" style="background:linear-gradient(135deg,#e8e6e2,#c9c6c0 50%,#eef1f3)"></div></div>
    <div class="event-body">
      <h2 class="event-title alt">Cum sociis natoque</h2>
      <p class="event-date">Oct 10, 2013</p>
      <p class="event-text">Quisque feugiat lacus vitae posuere blandit. Nulla sit amet laoreet felis, id rhoncus nisl. Aenean fringilla quam in nibh egestas, in malesuada tortor accumsan. Donec non massa lacinia, commodo eros eget, rutrum arcu. Integer tincidunt, velit id eleifend congue, odio massa consequat mauris, a scelerisque nulla nulla eu nulla. Cras luctus pulvinar nibh...</p>
      <a class="learn-more" href="#" style="margin-top:12px">Learn More &nbsp;»</a>
    </div>
  </article>

  <article class="event" style="top:462px">
    <div class="event-photo"><div role="img" aria-label="Scientist in blue gloves using a pipette" style="background:linear-gradient(135deg,#6a6a6a,#2f5d9c 50%,#1d3f7a)"></div></div>
    <div class="event-body">
      <h2 class="event-title">Ut interdum</h2>
      <p class="event-date" style="margin-top:11px">Oct 10, 2013</p>
      <p class="event-text">Quisque feugiat lacus vitae posuere blandit. Nulla sit amet laoreet felis, id rhoncus nisl. Aenean fringilla quam in nibh egestas, in malesuada tortor accumsan. Donec non massa lacinia, commodo eros eget, rutrum arcu. Integer tincidunt, velit id eleifend congue, odio massa consequat mauris, a scelerisque nulla nulla eu nulla. Cras luctus pulvinar nibh...</p>
      <a class="learn-more" href="#">Learn More &nbsp;»</a>
    </div>
  </article>

  <article class="event" style="top:664px">
    <div class="event-photo"><div role="img" aria-label="Researcher in safety glasses looking at a microscope" style="background:linear-gradient(135deg,#e9ecee,#d8d4cf 55%,#c9b6a4)"></div></div>
    <div class="event-body">
      <h2 class="event-title">Lorem ipsum dolor</h2>
      <p class="event-date">Oct 10, 2013</p>
      <p class="event-text">Quisque feugiat lacus vitae posuere blandit. Nulla sit amet laoreet felis, id rhoncus nisl. Aenean fringilla quam in nibh egestas, in malesuada tortor accumsan. Donec non massa lacinia, commodo eros eget, rutrum arcu. Integer tincidunt, velit id eleifend congue, odio massa consequat mauris, a scelerisque nulla nulla eu nulla. Cras luctus pulvinar nibh...</p>
      <a class="learn-more" href="#">Learn More &nbsp;»</a>
    </div>
  </article>

  <article class="event" style="top:866px">
    <div class="event-photo"><div role="img" aria-label="Two scientists in caps and masks working at microscopes" style="background:linear-gradient(135deg,#cfe2f1,#9fbfd6 45%,#e8eef3)"></div></div>
    <div class="event-body">
      <h2 class="event-title">Lorem ipsum dolor</h2>
      <p class="event-date">Oct 10, 2013</p>
      <p class="event-text">Quisque feugiat lacus vitae posuere blandit. Nulla sit amet laoreet felis, id rhoncus nisl. Aenean fringilla quam in nibh egestas, in malesuada tortor accumsan. Donec non massa lacinia, commodo eros eget, rutrum arcu. Integer tincidunt, velit id eleifend congue, odio massa consequat mauris, a scelerisque nulla nulla eu nulla. Cras luctus pulvinar nibh...</p>
      <a class="learn-more" href="#">Learn More &nbsp;»</a>
    </div>
  </article>
</main>

<footer class="site-footer">
  <nav class="footer-nav">
    <a href="#">Company</a><span>-</span><a href="#">Products &amp; Services</a><span>-</span><a href="#">Learning Center</a><span>-</span><a href="#">Events</a><span>-</span><a href="#">KVR News</a><span>-</span><a href="#">Contact</a>
  </nav>
  <div class="social" aria-label="Social links"><span></span><span></span><span></span></div>
  <p class="copyright">Copyright © <em>KVR Inc.</em> 2013</p>
</footer>
</body>
</html>
```